Looking for business card/letterhead/email signature

Take existing logo and create full design suite of collateral

Contact Information for Business Card

Use mock details that can be edited by us

Font styles to use
Sans Serif

```html
<!DOCTYPE html>
<html lang="en">
<head>
<meta charset="utf-8">
<title>Harlow Digital Stationery</title>
<link href="https://fonts.googleapis.com/css2?family=Lato:wght@400;700&family=Great+Vibes&display=swap" rel="stylesheet">
<style>
:root{
  --navy:#0e4a8c;
  --ink:#5b5d60;
  --paper:#ececec;
  --band:#e2e2e3;
  --stage:#dcdddf;
  --accent-blue:#2aa4dc;
  --accent-pink:#e0307a;
  --accent-lime:#b9cc3a;
}
*{margin:0;padding:0;box-sizing:border-box}
html,body{width:1200px;height:940px;overflow:hidden}
body{background:var(--stage);font-family:'Lato',sans-serif;color:var(--ink);position:relative}
.sheet{position:absolute;background:var(--paper);box-shadow:0 3px 10px rgba(0,0,0,.18)}
.wordmark{font-weight:700;color:var(--navy);display:flex;align-items:center;gap:5px;letter-spacing:-.5px}
.wordmark .dot{border-radius:50%;background:var(--navy)}
.icon{width:8px;height:8px;vertical-align:-1px;margin-right:3px;fill:none;stroke:var(--navy);stroke-width:1.3}
.contact-list{list-style:none}

/* business card front */
.card-front{left:226px;top:70px;width:286px;height:175px}
.card-front .wordmark{position:absolute;left:32px;top:76px;font-size:25px}
.card-front .wordmark .dot{width:9px;height:9px}
.card-front .person{position:absolute;left:167px;top:44px}
.card-front .name{font-size:9px;font-weight:700;color:var(--navy)}
.card-front .role{font-size:6.5px}
.card-front .address{position:absolute;left:167px;top:71px;font-size:6.5px;line-height:8.6px}
.card-front .contact-list{position:absolute;left:167px;top:96px;font-size:6.5px;line-height:8.8px}
.card-front .icon{width:6px;height:6px;margin-right:2px}

/* business card back */
.card-back{left:226px;top:290px;width:286px;height:175px;background:var(--navy)}
.card-back .wordmark{position:absolute;left:0;right:0;top:62px;justify-content:center;color:#fff;font-size:34px}
.card-back .wordmark .dot{width:11px;height:11px;background:#fff}
.card-back .web{position:absolute;left:0;right:0;top:148px;text-align:center;color:#fff;font-size:6.5px;letter-spacing:.6px}
.card-back .web b{font-weight:700}

/* email signature */
.signature{left:74px;top:510px;width:430px;height:134px}
.signature .wordmark{position:absolute;left:18px;top:44px;font-size:27px}
.signature .wordmark .dot{width:9px;height:9px}
.signature .social{position:absolute;left:44px;top:101px;display:flex;gap:5px}
.signature .social span{width:13px;height:13px;border-radius:50%;background:var(--navy)}
.signature .divider{position:absolute;left:136px;top:20px;width:2px;height:104px;background:var(--navy)}
.signature .details{position:absolute;left:152px;top:16px;font-size:12px;line-height:13.6px}
.signature .name{font-size:14px;font-weight:700;color:var(--navy);line-height:18px}
.signature .role{margin-bottom:5px}
.signature .icon{width:10px;height:10px;margin-right:4px}

/* letterhead */
.letterhead{left:561px;top:71px;width:564px;height:798px;overflow:hidden}
.letterhead .wordmark{position:absolute;left:35px;top:45px;font-size:32px}
.letterhead .wordmark .dot{width:11px;height:11px}
.letterhead .header-contact{position:absolute;left:420px;top:25px;font-size:9.6px;line-height:11.6px}
.letterhead .band{position:absolute;left:0;top:265px;width:100%;height:268px;background:var(--band)}
.letter{position:absolute;left:62px;top:178px;width:440px;font-size:8.8px;line-height:11.45px;text-align:justify}
.letter .date{margin-bottom:23px}
.letter .greeting{margin-bottom:11px}
.letter p.body{margin-bottom:11px}
.sign-off{position:absolute;left:62px;top:543px;font-size:8.8px;line-height:11.2px}
.sign-off .script{font-family:'Great Vibes',cursive;font-size:20px;color:#333;line-height:24px;margin:4px 0 -2px}
.corner-deco{position:absolute;right:0;bottom:0;width:254px;height:90px}
</style>
</head>
<body>

<section class="sheet card-front">
  <div class="wordmark"><span>harlow</span><span class="dot"></span></div>
  <div class="person">
    <div class="name">Nora J. Harlow</div>
    <div class="role">Managing Director</div>
  </div>
  <div class="address">Co.Street, Building/Suite<br>City/State, Zip Code</div>
  <ul class="contact-list">
    <li><svg class="icon" viewBox="0 0 10 10"><path d="M2 1l2 2-1 1.5c.8 1.5 1.5 2.2 3 3L7.5 6l2 2-1.5 1.5C4 9 1 6 .5 2z"/></svg>555.210.4400</li>
    <li><svg class="icon" viewBox="0 0 10 10"><rect x="2.5" y=".8" width="5" height="8.4" rx="1"/></svg>555.310.6600</li>
    <li><svg class="icon" viewBox="0 0 10 10"><rect x=".8" y="2" width="8.4" height="6"/><path d="M.8 2l4.2 3.4L9.2 2"/></svg>info@harlow-digital.com</li>
    <li><svg class="icon" viewBox="0 0 10 10"><circle cx="5" cy="5" r="4.2"/><path d="M.8 5h8.4M5 .8c-2.4 2.6-2.4 5.8 0 8.4M5 .8c2.4 2.6 2.4 5.8 0 8.4"/></svg>www.harlow-digital.com</li>
  </ul>
</section>

<section class="sheet card-back">
  <div class="wordmark"><span>harlow</span><span class="dot"></span></div>
  <div class="web">www.<b>harlow-digital</b>.com</div>
</section>

<section class="sheet signature">
  <div class="wordmark"><span>harlow</span><span class="dot"></span></div>
  <div class="social"><span></span><span></span><span></span></div>
  <div class="divider"></div>
  <div class="details">
    <div class="name">Nora J. Harlow</div>
    <div class="role">Managing Director</div>
    <ul class="contact-list">
      <li><svg class="icon" viewBox="0 0 10 10"><path d="M2 1l2 2-1 1.5c.8 1.5 1.5 2.2 3 3L7.5 6l2 2-1.5 1.5C4 9 1 6 .5 2z"/></svg>555.210.4400</li>
      <li><svg class="icon" viewBox="0 0 10 10"><rect x="2.5" y=".8" width="5" height="8.4" rx="1"/></svg>555.310.6600</li>
      <li><svg class="icon" viewBox="0 0 10 10"><rect x=".8" y="2" width="8.4" height="6"/><path d="M.8 2l4.2 3.4L9.2 2"/></svg>info@harlow-digital.com</li>
      <li><svg class="icon" viewBox="0 0 10 10"><circle cx="5" cy="5" r="4.2"/><path d="M.8 5h8.4M5 .8c-2.4 2.6-2.4 5.8 0 8.4M5 .8c2.4 2.6 2.4 5.8 0 8.4"/></svg>www.harlow-digital.com</li>
      <li>Co.Street, Building/Suite, City/State, Zip Code</li>
    </ul>
  </div>
</section>

<section class="sheet letterhead">
  <div class="band"></div>
  <div class="wordmark"><span>harlow</span><span class="dot"></span></div>
  <div class="header-contact">
    Co.Street, Building/Suite<br>City/State, Zip Code
    <ul class="contact-list">
      <li><svg class="icon" viewBox="0 0 10 10"><path d="M2 1l2 2-1 1.5c.8 1.5 1.5 2.2 3 3L7.5 6l2 2-1.5 1.5C4 9 1 6 .5 2z"/></svg>555.210.4400</li>
      <li><svg class="icon" viewBox="0 0 10 10"><rect x="2.5" y=".8" width="5" height="8.4" rx="1"/></svg>555.310.6600</li>
      <li><svg class="icon" viewBox="0 0 10 10"><rect x=".8" y="2" width="8.4" height="6"/><path d="M.8 2l4.2 3.4L9.2 2"/></svg>info@harlow-digital.com</li>
      <li><svg class="icon" viewBox="0 0 10 10"><circle cx="5" cy="5" r="4.2"/><path d="M.8 5h8.4M5 .8c-2.4 2.6-2.4 5.8 0 8.4M5 .8c2.4 2.6 2.4 5.8 0 8.4"/></svg>www.harlow-digital.com</li>
    </ul>
  </div>
  <article class="letter">
    <p class="date">January 01, 2020</p>
    <p class="greeting">Dear Lukas Brenner,</p>
    <p class="body">Lorem ipsum dolor sit amet, consectetuer adipiscing elit, sed diam nonummy nibh euismod tincidunt ut laoreet dolore magna aliquam erat volutpat. Ut wisi enim ad minim veniam, quis nostrud exerci tation ullamcorper suscipit lobortis nisl ut aliquip ex ea commodo consequat. Duis dolore te feugait nulla facilisi. Nam liber tempor cum soluta nobis eleifend option congue nihil imperdiet doming id quod mazim placerat facer possim assum. Duis autem vel eum iriure dolor in hendrerit in vulputate velit esse molestie consequat, vel illum dolore eu feugiat nulla facilisis at vero eros et accumsan et iusto odio dignissim qui blandit praesent luptatum zzril delenit augue duis dolore te feugait nulla facilisi. Consectetuer adipiscing elit, sed diam nonummy nibh euismod tincidunt ut laoreet dolore magna aliquam erat volutpat. Ut wisi enim ad minim veniam, quis nostrud exerci tation ullamcorper suscipit lobortis nisl ut aliquip ex ea commodo consequat.</p>
    <p class="body">Consectetuer adipiscing elit, sed diam nonummy nibh euismod tincidunt ut laoreet dolore magna aliquam erat volutpat. Ut wisi enim ad minim veniam, quis nostrud exerci tation ullamcorper suscipit lobortis nisl ut aliquip ex ea commodo consequat. Consectetuer adipiscing elit, sed diam nonummy nibh euismod tincidunt ut laoreet dolore magna aliquam erat volutpat. Ut wisi enim ad minim veniam, quis nostrud exerci tation ullamcorper suscipit lobortis nisl ut aliquip ex ea commodo consequat.</p>
    <p class="body">Dolor sit amet, consectetuer adipiscing elit, sed diam nonummy nibh euismod tincidunt ut laoreet dolore magna aliquam erat volutpat. Ut wisi enim ad minim veniam, quis nostrud exerci tation ullamcorper suscipit lobortis nisl ut aliquip ex ea commodo consequat. Duis dolore te feugait nulla facilisi. Nam liber tempor cum soluta nobis eleifend option congue nihil imperdiet doming id quod mazim placerat facer possim assum. Duis dolore te feugait nulla facilisi. Nam liber tempor cum soluta nobis eleifend option congue nihil imperdiet doming id quod mazim placerat facer possim assum. Duis dolore te feugait nulla facilisi. Nam liber tempor cum soluta nobis eleifend option congue nihil imperdiet doming id quod mazim placerat facer possim assum.</p>
  </article>
  <div class="sign-off">
    <p>Sincerely Yours,</p>
    <p class="script">Martin Ostrova</p>
    <p>Authorized Managing Director</p>
    <p>Your Company Name</p>
  </div>
  <div class="corner-deco" role="img" aria-label="Brand colour decoration in the lower corner" style="background:linear-gradient(160deg,rgba(185,204,58,0) 30%,rgba(42,164,220,.35) 60%,rgba(224,48,122,.45))"></div>
</section>

</body>
</html>
```